Business card for law firm

Need business card for new law firm. Think confident, authoritative, conservative, but not stuffy or old-fashioned.

Contact Information for Business Card

Content for card - logo (uploaded), plus the following:

Paul Whitcombe (larger font)
Managing Partner (larger font, but not as large as name)
Level 9, 7 Ferris Lane
Sydney NSW 2000
Main Tel 02 9364 2710
Direct Tel 02 8472 3159
Email paul@qvlegal.com.au
www.qvlegal.com.au

Letterhead design should include logo plus:
Level 9, 7 Ferris Lane
Sydney NSW 2000
Tel 02 8472 3159
www.qvlegal.com.au

```html
<!DOCTYPE html>
<html lang="en">
<head>
<meta charset="utf-8">
<title>Quinvale Legal – Business Card</title>
<link rel="stylesheet" href="https://fonts.googleapis.com/css2?family=Cinzel:wght@400;500&family=Open+Sans:wght@400&display=swap">
<style>
  :root {
    --backdrop: #5b5b5b;
    --navy: #031b57;
    --black: #050505;
    --white: #ffffff;
    --ink: #111111;
  }
  * { margin: 0; padding: 0; box-sizing: border-box; }
  html, body { width: 1200px; height: 802px; overflow: hidden; background: var(--backdrop); }
  .stage {
    width: 1200px; height: 802px;
    display: flex; align-items: center; justify-content: center; gap: 40px;
  }
  .card {
    width: 540px; height: 324px; position: relative; overflow: hidden;
    box-shadow: 0 3px 8px rgba(0,0,0,.45);
  }
  /* Front: contact side */
  .card--front { background: var(--navy); }
  .card__block {
    position: absolute; left: 0; top: 0; width: 287px; height: 100%;
    background: var(--black);
  }
  .contact {
    position: absolute; right: 30px; top: 76px;
    text-align: right; color: var(--white);
    font-family: "Open Sans", sans-serif; font-size: 15px; line-height: 19.5px;
  }
  .contact__name {
    font-family: "Cinzel", serif; font-size: 21px; font-weight: 500;
    letter-spacing: .3px; line-height: 24px;
  }
  .contact__role { font-size: 15.5px; margin-bottom: 6px; }
  .contact__line { display: flex; justify-content: flex-end; align-items: center; gap: 3px; }
  .contact__line small { font-size: 11px; letter-spacing: .3px; }
  .contact__line svg { width: 12px; height: 12px; flex: none; }
  .contact__address { margin-top: 4px; }
  /* Back: brand side */
  .card--back { background: var(--white); }
  .brand {
    position: absolute; left: 0; right: 0; top: 79px; text-align: center; color: var(--ink);
  }
  .brand__mark { width: 60px; height: 60px; background: var(--navy); margin: 0 auto 26px; }
  .brand__name { font-family: "Cinzel", serif; font-size: 40px; font-weight: 400; line-height: 40px; letter-spacing: 1px; }
  .brand__sub { font-family: "Cinzel", serif; font-size: 14px; letter-spacing: 14px; margin-top: 6px; padding-left: 14px; }
</style>
</head>
<body>
<main class="stage">
  <section class="card card--front">
    <div class="card__block"></div>
    <div class="contact">
      <div class="contact__name">PAUL WHITCOMBE</div>
      <div class="contact__role">Managing Partner</div>
      <div class="contact__line">02 9364 2710
        <svg viewBox="0 0 12 12"><path fill="#fff" d="M1 4c0-2 2-3 5-3s5 1 5 3l-2 1-1-1.5H4L3 5zM3 6h6l1.5 5h-9z"/><circle cx="6" cy="8" r="1.3" fill="#031b57"/></svg>
      </div>
      <div class="contact__line">02 8472 3159 <small>(DIRECT)</small>
        <svg viewBox="0 0 12 12"><path fill="#fff" d="M1 4c0-2 2-3 5-3s5 1 5 3l-2 1-1-1.5H4L3 5zM3 6h6l1.5 5h-9z"/><circle cx="6" cy="8" r="1.3" fill="#031b57"/></svg>
      </div>
      <div class="contact__line">paul@qvlegal.com.au
        <svg viewBox="0 0 12 12"><rect x="1" y="2.5" width="10" height="7" fill="#fff"/><path d="M1.5 3l4.5 3.5L10.5 3" fill="none" stroke="#031b57" stroke-width="1"/></svg>
      </div>
      <div class="contact__line">www.qvlegal.com.au
        <svg viewBox="0 0 12 12"><circle cx="6" cy="6" r="5" fill="#fff"/><path d="M3.5 4.5l2 .5 .5 2-1.5 1M7 3l1.5 1.5L8 6l1.5 1" fill="none" stroke="#031b57" stroke-width="1"/></svg>
      </div>
      <div class="contact__address">Level 9, 7 Ferris Lane<br>Sydney NSW 2000</div>
    </div>
  </section>

  <section class="card card--back">
    <div class="brand">
      <div class="brand__mark"></div>
      <div class="brand__name">QUINVALE</div>
      <div class="brand__sub">LEGAL</div>
    </div>
  </section>
</main>
</body>
</html>
```